Presentation Brochure and Sample Box Design for Kovo Slate

Kovo Slate is a colour coated solid aluminium panel that our company supplies to the signage and building cladding industries.
We require an, A4 double-sided folding brochure (swatch book) that folds 3 ways, opening once and then a second time to lay out 3 pages flat.

There should be a front and back cover.

The inside cover should be reserved with text blocks for written information about the panel.

The opposite page on the right when you first open the brochure should have all our Matte PVDF 2mm colours which you will find in the attached PDF of colour swatches and details.

When the brochure is folded out a second time, showing all three inside pages flat, the two inside pages on the right (next to the inside cover with the written information) should show all our FEVE Gloss 1.6mm colours which you will also find in the attached PDF colour book.

This brochure should have a modern and professional feel suitable for presenting to architects and designers.

We also require a box design to contain aluminium samples of all the colours in the range.

Please refer to the template attached for the box dimensions and layout.

The box should tie in with the brochure as a complete package with a modern and professional look suitable for presenting to architects and designers.

Finally we require a small label sticker to be stuck on the back of each sample. On the sticker should be the Kovo Slate logo, a space to put the product code for the sample colour and the phone number 1300 584 362.

To summarise, this package project includes:
1 tri-folding A4 brochure,
1 sample box package design,
1 sample sticker label.

This is our signature new product that we will be marketing to signage installers to create coloured and printed aluminium signs. We are also looking to move further into the building and architectural market place with this product.

Please refer to the attachments for the Kovo Slate logo - the colour swatch book and template for the sample box.
The Kovo Slate logo can be shown in White, Black or Silver.

Target Market(s)

Architects, interior designers, builders and signage installers.

Font styles to use
Serif
Sans Serif

Requirements
Must have
• A modern, neat and professional upmarket look suitable for presenting to architects.
Nice to have
• A slick and classy look that makes you want to take home the box or brochure even if you're not interested in the product.
Should not have
• A cheap, untidy, low market look with too many colours.

```html
<!DOCTYPE html>
<html lang="en">
<head>
<meta charset="utf-8">
<title>Kovo Slate – Brochure, Sample Box and Sticker</title>
<link href="https://fonts.googleapis.com/css2?family=Josefin+Sans:wght@300;400&family=Montserrat:wght@400;500;600&family=Oswald:wght@400;500&display=swap" rel="stylesheet">
<style>
:root{
  --stage:#c6c7c9;
  --ink:#0b1015;
  --navy:#15212a;
  --steel:#2b4553;
  --gold:#eadb9f;
  --bronze:#c29b55;
  --teal:#5f93a8;
  --deep-teal:#2f5d73;
  --paper:#ffffff;
  --band:#ececec;
  --text-light:#d9dde0;
  --rule:rgba(255,255,255,.22);
}
*{box-sizing:border-box;margin:0;padding:0}
html,body{width:1200px;height:803px;overflow:hidden}
body{background:var(--stage);font-family:"Montserrat",sans-serif;color:var(--text-light);position:relative}

/* ---------- shared lockup ---------- */
.brand{font-family:"Montserrat",sans-serif;font-weight:600;color:#fff;letter-spacing:1px;white-space:nowrap}
.title-colour{font-family:"Josefin Sans",sans-serif;font-weight:300;color:var(--gold);line-height:.95;letter-spacing:1px;white-space:nowrap}
.title-coated{font-family:"Oswald",sans-serif;font-weight:500;color:var(--teal);line-height:1;letter-spacing:1px;white-space:nowrap}
.title-sub{font-family:"Montserrat",sans-serif;font-weight:500;color:#fff;letter-spacing:4px;text-transform:uppercase;white-space:nowrap}
.photo{background:
  linear-gradient(115deg,rgba(255,255,255,.05) 0 30%,transparent 30% 55%,rgba(255,255,255,.04) 55% 70%,transparent 70%),
  linear-gradient(160deg,#1c2a33 0%,#2c4857 38%,#17252e 68%,#0a1015 100%)}

/* ---------- brochure outside ---------- */
.brochure{position:absolute;top:16px;width:555px;height:375px;display:flex;overflow:hidden}
.brochure--outside{left:20px;background:var(--ink)}
.brochure--outside .photo{position:absolute;left:185px;top:0;width:370px;height:100%}
.panel{position:relative;width:185px;height:100%;flex:none}
.panel + .panel{border-left:1px solid rgba(255,255,255,.06)}

.back-flap{background:var(--ink);padding:30px 18px 0}
.kicker{display:flex;align-items:flex-start;gap:5px}
.kicker__mark{width:12px;height:16px;flex:none;margin-top:4px}
.kicker__title{font-family:"Josefin Sans",sans-serif;font-weight:300;font-size:26px;color:var(--gold);line-height:1}
.kicker__sub{font-family:"Oswald",sans-serif;font-size:14px;color:var(--teal);letter-spacing:.5px}
.kicker__spaced{font-size:6.5px;letter-spacing:3px;color:#fff;text-transform:uppercase;margin-top:3px}
.kicker--right{justify-content:flex-end;text-align:right;margin-top:36px}
.kicker--right .kicker__title{font-size:18px}
.kicker--right .kicker__sub{font-size:11px}
.intro{font-style:italic;font-size:9.5px;color:#fff;line-height:1.35;margin-top:34px}
.body-copy{font-size:7.2px;line-height:1.5;color:var(--text-light);margin-top:12px}

.back-panel{padding:0 20px}
.contact__title{position:absolute;top:86px;left:26px;font-family:"Oswald",sans-serif;font-weight:500;font-size:22px;color:#fff;line-height:1;letter-spacing:1px}
.social{position:absolute;top:150px;left:26px;list-style:none}
.social li{display:flex;align-items:center;gap:8px;font-size:7.5px;font-weight:600;letter-spacing:1.5px;color:#fff;margin-bottom:9px;text-transform:uppercase}
.social__dot{width:7px;height:7px;border:1px solid var(--gold);border-radius:50%}
.back-panel__footer{position:absolute;left:26px;top:262px}
.back-panel__footer .brand{font-size:20px}
.back-panel__footer p{font-size:7.5px;color:#fff;margin-top:5px;line-height:1.4}
.phone{font-family:"Oswald",sans-serif;color:var(--gold);font-size:15px;letter-spacing:1px;margin-top:5px;white-space:nowrap}
.web{font-size:7px;letter-spacing:1px;color:#fff}

.front-cover{background:linear-gradient(180deg,rgba(5,9,12,.75),rgba(8,14,18,.35) 60%,rgba(5,9,12,.7));overflow:hidden}
.front-cover__lockup{position:absolute;top:96px;left:18px;right:14px}
.front-cover__lockup .brand{font-size:21px}
.front-cover__lockup .title-colour{font-size:38px;margin-top:30px}
.front-cover__lockup .title-coated{font-size:24px;margin-top:2px}
.front-cover__lockup .title-sub{font-size:7px;margin-top:8px;letter-spacing:4px}

/* ---------- brochure inside ---------- */
.brochure--inside{left:625px;background:var(--paper);border-top:7px solid var(--ink);border-bottom:7px solid var(--ink)}
.brochure--inside .panel{padding:0 12px;color:#222}
.brochure--inside .panel + .panel{border-left:1px solid #e2e2e2}
.mini-lockup{text-align:center}
.mini-lockup .brand{color:#111;font-size:11px}
.mini-lockup .title-colour{color:var(--bronze);font-size:22px;margin-top:3px}
.mini-lockup .title-coated{color:var(--deep-teal);font-size:14px}
.mini-lockup .title-sub{color:#333;font-size:5.5px;margin-top:2px}
.range{background:var(--band);font-size:6.2px;letter-spacing:1.8px;text-align:center;padding:4px 0;color:#333;position:relative;margin:10px 0 10px;text-transform:uppercase;white-space:nowrap}
.range::after{content:"";position:absolute;left:50%;bottom:-6px;margin-left:-5px;border-left:5px solid transparent;border-right:5px solid transparent;border-top:6px solid var(--bronze)}
.swatches{display:grid;grid-template-columns:repeat(5,1fr);gap:5px}
.swatches--three{grid-template-columns:repeat(3,29px);justify-content:center}
.swatch{height:34px;display:flex;align-items:flex-end;justify-content:center;padding-bottom:3px;font-size:4px;font-weight:600;letter-spacing:.3px;text-transform:uppercase;color:#fff}
.swatch--light{color:#222;box-shadow:inset 0 0 0 1px #d6d6d6}
.swatches--short .swatch{height:28px}

/* ---------- section labels ---------- */
.label{position:absolute;font-size:10px;letter-spacing:3px;color:#333}
.label--box-net{left:32px;top:600px;transform:rotate(-90deg)}
.label--sticker{left:406px;top:680px}
.label--box{left:870px;top:440px}

/* ---------- box net ---------- */
.box-net{position:absolute;left:75px;top:414px;width:200px;height:372px;background:var(--ink)}
.box-net__section{position:absolute;left:0;width:100%;border-bottom:1px solid var(--rule)}
.strip{top:0;height:62px;display:flex;align-items:center;gap:6px;padding:0 7px}
.strip--flipped{top:158px;transform:rotate(180deg);background:var(--ink)}
.strip .brand{font-size:5.5px}
.strip .title-colour{font-size:9px}
.strip .title-coated{font-size:6px}
.strip .title-sub{font-size:2.4px;letter-spacing:1.2px}
.strip__info{flex:1;display:flex;gap:5px;align-items:center;justify-content:space-between;font-size:2.6px;color:#fff;white-space:nowrap}
.strip__info .phone{font-size:4.6px;margin:0;letter-spacing:.3px}
.strip__social{list-style:none;font-size:2.8px;font-weight:600;letter-spacing:.5px;line-height:1.8;color:#fff;text-transform:uppercase}
.blank-face{top:62px;height:96px;background:linear-gradient(90deg,#0b1015 0 50%,#16252e 50%)}
.face-front{top:220px;height:102px;display:flex;align-items:center;justify-content:center;text-align:center}
.face-front .brand{font-size:15px}
.face-front .title-colour{font-size:19px;margin-top:8px}
.face-front .title-coated{font-size:13px}
.face-front .title-sub{font-size:3.5px;margin-top:4px;letter-spacing:2.5px}
.flap{top:322px;height:50px;border:none;clip-path:polygon(0 0,100% 0,100% 70%,50% 100%,0 70%)}

/* ---------- stickers ---------- */
.stickers{position:absolute;left:340px;top:540px;display:flex;gap:10px}
.sticker{width:96px;height:96px;border-radius:50%;background:var(--ink);display:flex;flex-direction:column;align-items:center;justify-content:center;text-align:center}
.sticker .brand{font-size:8px}
.sticker .title-colour{font-size:10px;margin-top:2px}
.sticker .title-coated{font-size:6.5px}
.sticker .title-sub{font-size:2.5px;letter-spacing:1.5px}
.sticker__field{font-size:3.5px;letter-spacing:1.2px;color:#fff;margin-top:5px;text-transform:uppercase}
.sticker__code{width:60px;height:8px;background:#fff;margin-top:3px}
.sticker__phone{display:flex;align-items:center;gap:2px;font-family:"Oswald",sans-serif;font-size:5.5px;color:var(--gold);margin-top:1px}
.sticker__phone svg{width:5px;height:5px}

/* ---------- box lid ---------- */
.box-lid{position:absolute;left:650px;top:470px;width:500px;height:230px;text-align:center;display:flex;align-items:center;justify-content:center}
.box-lid .brand{font-size:30px}
.box-lid .title-colour{font-size:46px;margin-top:12px}
.box-lid .title-coated{font-size:30px}
.box-lid .title-sub{font-size:8px;margin-top:8px;letter-spacing:6px}
.box-side{position:absolute;left:650px;top:700px;width:500px;height:46px;background:var(--navy);display:flex;align-items:center;justify-content:space-between;padding:0 16px;border-top:1px solid var(--rule)}
.box-side__lockup{display:flex;align-items:baseline;gap:6px}
.box-side .title-colour{font-size:16px}
.box-side .title-coated{font-size:11px}
.box-side__info{display:flex;gap:14px;align-items:center;font-size:6px;color:#fff;white-space:nowrap}
.box-side__info .phone{font-size:9px;margin:0}
</style>
</head>
<body>

<!-- Brochure: outside spread -->
<section class="brochure brochure--outside" aria-label="Brochure outside spread">
  <div class="photo" role="img" aria-label="Architectural photograph of a glass office tower seen from below"></div>

  <article class="panel back-flap">
    <div class="kicker">
      <svg class="kicker__mark" viewBox="0 0 12 16" aria-hidden="true"><polygon points="0,0 12,8 0,16 4,8" fill="#5f93a8"/></svg>
      <div>
        <h2 class="kicker__title">LOREMIP</h2>
        <p class="kicker__sub">DOLOR SIT AMETOR</p>
        <p class="kicker__spaced">Consecte tuerda</p>
      </div>
    </div>
    <div class="kicker kicker--right">
      <div>
        <h2 class="kicker__title">IPSUMAR</h2>
        <p class="kicker__sub">DOLORSIT AM</p>
      </div>
      <svg class="kicker__mark" viewBox="0 0 12 16" aria-hidden="true"><polygon points="0,0 12,8 0,16 4,8" fill="#eadb9f"/></svg>
    </div>
    <p class="intro">Lorem ipsum dolor sit amet, con sectetuer adipiscing elit, sed</p>
    <p class="body-copy">Lorem ipsum dolor sit amet, consectetuer adipiscing elit, sed diam nonummy nibh euismod tincidunt ut laoreet dolore magna aliquam erat volutpat. Ut wisi enim ad minim veniam, quis nostrud exerci tation ullamcorper suscipit lobortis nisl ut aliquip ex ea commodo consequat. Duis autem vel eum iriure dolor in</p>
  </article>

  <article class="panel back-panel">
    <h2 class="contact__title">CONTACT<br>US</h2>
    <ul class="social">
      <li><span class="social__dot"></span>Snapgrid</li>
      <li><span class="social__dot"></span>Friendwall</li>
      <li><span class="social__dot"></span>Chirpline</li>
    </ul>
    <div class="back-panel__footer">
      <p class="brand">Kovo Slate</p>
      <p>Lorem ipsum dolor sit amet,<br>consectetuer.</p>
      <p class="phone">1300 584 362</p>
      <p class="web">www.kovoslate.com</p>
    </div>
  </article>

  <article class="panel front-cover">
    <div class="front-cover__lockup">
      <p class="brand">Kovo Slate</p>
      <h1 class="title-colour">COLOUR</h1>
      <p class="title-coated">COATED SOLID</p>
      <p class="title-sub">Aluminium panel</p>
    </div>
  </article>
</section>

<!-- Brochure: inside spread -->
<section class="brochure brochure--inside" aria-label="Brochure inside spread">
  <article class="panel">
    <div class="mini-lockup" style="margin-top:18px">
      <p class="brand">Kovo Slate</p>
      <p class="title-colour">COLOUR</p>
      <p class="title-coated">COATED SOLID</p>
      <p class="title-sub">Aluminium</p>
    </div>
    <h3 class="range">Feve Gloss 1.6 mm</h3>
    <div class="swatches">
      <span class="swatch swatch--light" style="background:#fff">White</span>
      <span class="swatch" style="background:#111">Black</span>
      <span class="swatch" style="background:#c8202f">Red</span>
      <span class="swatch swatch--light" style="background:#e7d62a">Yellow</span>
      <span class="swatch" style="background:#1e73be">Blue</span>
      <span class="swatch" style="background:#1f2f6b">Navy</span>
      <span class="swatch" style="background:#174d35">Forest</span>
      <span class="swatch" style="background:#7a1d2c">Maroon</span>
      <span class="swatch" style="background:#e2552a">Orange</span>
      <span class="swatch" style="background:#e07a2b">Pumpkin</span>
      <span class="swatch" style="background:#172a4f">Midnight</span>
      <span class="swatch" style="background:#1f4f7a">Lagoon</span>
      <span class="swatch" style="background:#1d3760">Galaxy</span>
      <span class="swatch" style="background:#0e7c86">Turquoise</span>
      <span class="swatch" style="background:#1f9a45">Green</span>
      <span class="swatch swatch--light" style="background:#d8c79a">Ivory</span>
      <span class="swatch" style="background:#159a4a">Emerald</span>
      <span class="swatch" style="background:#4cae4c">Apple</span>
      <span class="swatch" style="background:#d6232f">Scarlet</span>
      <span class="swatch" style="background:#f0a21c">Mustard</span>
      <span class="swatch" style="background:#6a2e8c">Violet</span>
      <span class="swatch" style="background:#8cc63f">Lime</span>
      <span class="swatch" style="background:#3aa657">Spring</span>
      <span class="swatch" style="background:#d61a6b">Fuchsia</span>
      <span class="swatch" style="background:#b0203c">Plum</span>
    </div>
  </article>

  <article class="panel">
    <h3 class="range" style="margin-top:12px">Feve Gloss 1.6 mm</h3>
    <div class="swatches swatches--short">
      <span class="swatch swatch--light" style="background:#f1e03a">Lemon</span>
      <span class="swatch" style="background:#1d4f9e">Cobalt</span>
      <span class="swatch swatch--light" style="background:#7fb8e0">Azure</span>
      <span class="swatch" style="background:#4f7a6a">Sage</span>
      <span class="swatch" style="background:#5a6670">Steel</span>
      <span class="swatch" style="background:#8d9296">Grey</span>
      <span class="swatch swatch--light" style="background:#c4c6c8">Silver</span>
      <span class="swatch" style="background:#8a7d6d">Taupe</span>
      <span class="swatch swatch--light" style="background:#b9b2a4">Stone</span>
      <span class="swatch" style="background:#6d5a4c">Mocha</span>
      <span class="swatch" style="background:#5b2a22">Chocolate</span>
      <span class="swatch" style="background:#3b2f6a">Indigo</span>
      <span class="swatch" style="background:#f0a020">Amber</span>
      <span class="swatch" style="background:#8a8c8e">Ash</span>
      <span class="swatch swatch--light" style="background:#d9ceb4">Sand</span>
    </div>
    <div class="mini-lockup" style="margin-top:12px">
      <p class="brand">Kovo Slate</p>
      <p class="title-colour">COLOUR</p>
      <p class="title-coated">COATED SOLID</p>
      <p class="title-sub">Aluminium</p>
    </div>
    <h3 class="range">Metallics &amp; Pearls 1.6 mm</h3>
    <div class="swatches">
      <span class="swatch swatch--light" style="background:#c9b58a">Gold</span>
      <span class="swatch" style="background:#a68a5e">Bronze</span>
      <span class="swatch" style="background:#8e8e8c">Pewter</span>
      <span class="swatch swatch--light" style="background:#d8cfb8">Champagne</span>
      <span class="swatch" style="background:#9a9c9e">Titanium</span>
      <span class="swatch swatch--light" style="background:#e8e6e0">Pearl</span>
      <span class="swatch swatch--light" style="background:#f2f2f2">Frost</span>
      <span class="swatch swatch--light" style="background:#c8c9cb">Silver</span>
      <span class="swatch swatch--light" style="background:#d9d6d0">Quartz</span>
      <span class="swatch swatch--light" style="background:#c5ccd2">Mist</span>
    </div>
  </article>

  <article class="panel">
    <h3 class="range" style="margin-top:12px">Metallics &amp; Pearls 1.6 mm</h3>
    <div class="swatches swatches--three swatches--short">
      <span class="swatch" style="background:#1b1b1b">Ebony</span>
      <span class="swatch" style="background:#c07a45">Copper</span>
      <span class="swatch" style="background:#b08a58">Brass</span>
    </div>
    <div class="mini-lockup" style="margin-top:14px">
      <p class="brand">Kovo Slate</p>
      <p class="title-colour">COLOUR</p>
      <p class="title-coated">COATED SOLID</p>
      <p class="title-sub">Aluminium</p>
    </div>
    <h3 class="range">PVDF Matte 2 mm</h3>
    <div class="swatches">
      <span class="swatch swatch--light" style="background:#fff">Snow</span>
      <span class="swatch" style="background:#111">Onyx</span>
      <span class="swatch" style="background:#c62030">Ruby</span>
      <span class="swatch" style="background:#1f3f8f">Cobalt</span>
      <span class="swatch" style="background:#d5232c">Carmine</span>
      <span class="swatch" style="background:#1b2a50">Navy</span>
      <span class="swatch" style="background:#20437a">Ocean</span>
      <span class="swatch swatch--light" style="background:#ddd0a8">Cream</span>
      <span class="swatch" style="background:#f0a01e">Saffron</span>
      <span class="swatch" style="background:#c01f2e">Crimson</span>
      <span class="swatch" style="background:#2e3236">Charcoal</span>
      <span class="swatch" style="background:#6a7278">Slate</span>
      <span class="swatch swatch--light" style="background:#a8adb0">Pebble</span>
      <span class="swatch swatch--light" style="background:#e6cf1f">Canary</span>
      <span class="swatch" style="background:#1b5aa8">Royal</span>
    </div>
  </article>
</section>

<!-- Box dieline -->
<p class="label label--box-net">BOX</p>
<section class="box-net" aria-label="Sample box dieline">
  <div class="box-net__section strip">
    <div>
      <p class="brand">Kovo Slate</p>
      <p class="title-colour">COLOUR</p>
      <p class="title-coated">COATED SOLID</p>
      <p class="title-sub">Aluminium panel</p>
    </div>
    <div class="strip__info">
      <span>Lorem ipsum dolor sit amet</span>
      <span class="phone">1300 584 362</span>
      <span>www.kovoslate.com</span>
    </div>
    <ul class="strip__social"><li>Snapgrid</li><li>Friendwall</li><li>Chirpline</li></ul>
  </div>
  <div class="box-net__section blank-face"></div>
  <div class="box-net__section strip strip--flipped">
    <div>
      <p class="brand">Kovo Slate</p>
      <p class="title-colour">COLOUR</p>
      <p class="title-coated">COATED SOLID</p>
      <p class="title-sub">Aluminium panel</p>
    </div>
    <div class="strip__info">
      <span>Lorem ipsum dolor sit amet</span>
      <span class="phone">1300 584 362</span>
      <span>www.kovoslate.com</span>
    </div>
    <ul class="strip__social"><li>Snapgrid</li><li>Friendwall</li><li>Chirpline</li></ul>
  </div>
  <div class="box-net__section face-front photo" role="img" aria-label="Architectural photograph of glass facade framing, with product title">
    <div>
      <p class="brand">Kovo Slate</p>
      <p class="title-colour">COLOUR</p>
      <p class="title-coated">COATED SOLID</p>
      <p class="title-sub">Aluminium panel</p>
    </div>
  </div>
  <div class="box-net__section flap photo" role="img" aria-label="Continuation of the glass facade photograph"></div>
</section>

<!-- Stickers -->
<section class="stickers" aria-label="Sample sticker labels">
  <div class="sticker">
    <p class="brand">Kovo Slate</p>
    <p class="title-colour">COLOUR</p>
    <p class="title-coated">COATED SOLID</p>
    <p class="title-sub">Aluminium panel</p>
    <p class="sticker__field">Product code:</p>
    <span class="sticker__code"></span>
    <p class="sticker__field">Contact us:</p>
    <p class="sticker__phone"><svg viewBox="0 0 10 10" aria-hidden="true"><path d="M2 1l2 2-1 1.5c.6 1.2 1.3 1.9 2.5 2.5L7 6l2 2-1.2 1.2C4.5 9 1 5.5.8 2.2z" fill="#eadb9f"/></svg>1300 584 362</p>
  </div>
  <div class="sticker photo">
    <p class="brand">Kovo Slate</p>
    <p class="title-colour">COLOUR</p>
    <p class="title-coated">COATED SOLID</p>
    <p class="title-sub">Aluminium panel</p>
    <p class="sticker__field">Product code:</p>
    <span class="sticker__code"></span>
    <p class="sticker__field">Contact us:</p>
    <p class="sticker__phone"><svg viewBox="0 0 10 10" aria-hidden="true"><path d="M2 1l2 2-1 1.5c.6 1.2 1.3 1.9 2.5 2.5L7 6l2 2-1.2 1.2C4.5 9 1 5.5.8 2.2z" fill="#eadb9f"/></svg>1300 584 362</p>
  </div>
</section>
<p class="label label--sticker">STICKER</p>

<!-- Box lid and side -->
<p class="label label--box">BOX</p>
<section class="box-lid photo" role="img" aria-label="Architectural photograph of a glass tower, with product title on the box lid">
  <div>
    <p class="brand">Kovo Slate</p>
    <p class="title-colour">COLOUR</p>
    <p class="title-coated">COATED SOLID</p>
    <p class="title-sub">Aluminium panel</p>
  </div>
</section>
<section class="box-side" aria-label="Box side">
  <div class="box-side__lockup">
    <p class="title-colour">COLOUR</p>
    <p class="title-coated">COATED SOLID</p>
  </div>
  <div class="box-side__info">
    <span>Lorem ipsum dolor sit amet, consectetuer</span>
    <span class="phone">1300 584 362</span>
    <span>www.kovoslate.com</span>
  </div>
</section>

</body>
</html>
```